accomplished personal trainer, former elite gymnast from Russia, highly professional and experienced

Established Fitness trainer in California requires a new web site to attract personal clients and build her group exercise classes.

Here is an example of another fitness trainer's site that I really liked the technology:
http://www.tedvorlam.com

Below I have inserted my current web site: www.quelbornfitnesslodi.com
You can use this web site for the principal content, such as my background and qualifications.

Target Market(s)

Anyone who wants to improve their fitness levels and wellness in general. Anyone who needs directions and instruction on how to exercise. I can train anyone from elite athlete to a disabled person.

Industry/Entity Type

Fitness

Coding

Coded - Design and coding required

Number of Pages Required

5+ page

Font styles to use
Sans Serif

Requirements
Must have
• Easy to navigate main info about me, location, services, contact, benefits of using my services.
• Would be great to create unique representation of me as a trainer and a person, using new technologies and new ideas. Make it different from the other websites. Having its own character. Not too complicated and heavy with information, but an eye catching, useful and fun to navigate.
Nice to have
• new technology, easy access to information, the idea of enjoyment of life, lightness about achieving any goal, spiritual wisdom, unique design. I am planning to insert educational videos, advise, maybe jokes. Sign in, shopping cart, logo, should be easy for me to make changes in content.
Should not have
• cliché, outdated technology, too complicated,

```html
<!DOCTYPE html>
<html lang="en">
<head>
<meta charset="utf-8">
<title>Quelborn Fitness Lodi</title>
<link rel="stylesheet" href="https://fonts.googleapis.com/css2?family=Montserrat:wght@400;600;700;800&family=Open+Sans:wght@400;600&display=swap">
<style>
:root{
  --ink:#1c1c1c;
  --muted:#6a6a6a;
  --soft:#efefef;
  --panel:#f4f4f4;
  --line:#2a2a2a;
  --white:#ffffff;
  --ghost:#dedede;
  --quote:#e8e8e8;
}
*{margin:0;padding:0;box-sizing:border-box}
html,body{width:1200px;height:2716px;overflow:hidden;background:var(--white)}
body{font-family:"Open Sans",sans-serif;color:var(--ink);position:relative}
.heading{font-family:"Montserrat",sans-serif;font-weight:800;text-transform:uppercase;letter-spacing:1px;line-height:1.1}
.btn{display:inline-block;font-family:"Montserrat",sans-serif;font-weight:700;font-size:12px;letter-spacing:1px;text-transform:uppercase;border:2px solid var(--line);padding:9px 13px;color:var(--ink)}
.para{font-size:13px;line-height:22px;color:var(--muted)}
.photo{position:absolute}

/* header + hero */
.hero{position:absolute;left:0;top:0;width:1200px;height:545px;background:var(--soft);overflow:hidden}
.brand{position:absolute;left:40px;top:52px;font-family:"Montserrat",sans-serif;font-weight:700;font-size:22px;letter-spacing:1px}
.nav{position:absolute;right:40px;top:62px;display:flex;gap:28px;font-family:"Montserrat",sans-serif;font-size:11px;font-weight:600;letter-spacing:1px;text-transform:uppercase}
.ghost-word{position:absolute;left:580px;top:130px;font-family:"Montserrat",sans-serif;font-weight:800;font-size:150px;line-height:160px;color:var(--ghost);letter-spacing:4px}
.ghost-word span{display:block}
.hero-title{position:absolute;left:130px;top:188px;font-size:62px}
.hero .btn{position:absolute;left:130px;top:370px}
.dots{position:absolute;left:130px;top:452px;display:flex;gap:8px}
.dots i{width:10px;height:10px;border-radius:50%;border:1px solid var(--ink);display:block}
.dots i:first-child{background:var(--ink)}

/* shared section titles */
.section-title{font-size:30px;font-weight:400;margin-bottom:24px}
.section-title small{display:block;font-size:30px;font-weight:800}
.section-btn{margin-top:26px}

/* about */
.about-text{position:absolute;left:130px;top:615px;width:420px}

/* group */
.group-band{position:absolute;left:0;top:1015px;width:1200px;height:480px;background:var(--panel)}
.group-text{position:absolute;left:655px;top:1080px;width:430px}

/* personal */
.personal-band{position:absolute;left:0;top:1505px;width:600px;height:410px;background:var(--panel)}
.personal-text{position:absolute;left:130px;top:1570px;width:420px}

/* testimonials */
.testimonial-text{position:absolute;left:130px;top:1985px;width:400px;color:var(--white)}
.testimonial-text .para{color:var(--quote)}
.quote-name{margin-top:16px;font-family:"Montserrat",sans-serif;font-weight:700;font-size:12px;letter-spacing:1px;text-transform:uppercase}
.arrows{display:flex;gap:6px;margin-top:36px}
.arrows span{width:24px;height:18px;border:1px solid var(--white);display:flex;align-items:center;justify-content:center}

/* subscribe */
.subscribe{position:absolute;left:0;top:2335px;width:1200px;height:225px;background:var(--soft)}
.subscribe h2{position:absolute;left:0;width:1200px;top:58px;text-align:center;font-size:34px}
.form{position:absolute;left:150px;top:122px;display:flex;gap:18px}
.field{width:210px;height:44px;background:var(--white);border:1px solid #cfcfcf;font-size:12px;color:#9a9a9a;padding:13px 12px}
.submit{width:210px;height:44px;background:#111;color:var(--white);font-family:"Montserrat",sans-serif;font-weight:700;font-size:13px;letter-spacing:1px;display:flex;align-items:center;justify-content:center}

/* footer */
.footer-nav{position:absolute;left:0;width:1200px;top:2592px;display:flex;justify-content:center;gap:18px;font-family:"Montserrat",sans-serif;font-size:11px;font-weight:600;letter-spacing:1px;text-transform:uppercase}
.footer-nav span.sep{color:#aaa}
.social{position:absolute;left:0;width:1200px;top:2630px;display:flex;justify-content:center;gap:10px}
.social i{width:26px;height:26px;border-radius:50%;border:2px solid var(--ink);display:block}
.copyright{position:absolute;left:0;width:1200px;top:2672px;text-align:center;font-size:11px;color:var(--muted)}
</style>
</head>
<body>

<header class="hero">
  <div class="ghost-word" aria-hidden="true"><span>QUEL</span><span>BORN</span></div>
  <div class="brand">QUELBORN FITNESS LODI</div>
  <nav class="nav"><span>Group Classes</span><span>Personal Training</span><span>About Irina</span><span>Contact</span><span>Blog</span></nav>
  <h1 class="heading hero-title">Fitness<br>Outdoors</h1>
  <a class="btn">View Details</a>
  <div class="dots"><i></i><i></i><i></i></div>
  <svg class="photo" style="left:640px;top:150px" width="250" height="395" role="img" aria-label="Smiling trainer in pink top posing outdoors">
    <defs><linearGradient id="heroG" x1="0" y1="0" x2="0" y2="1"><stop offset="0" stop-color="#e3c9a4"/><stop offset="0.5" stop-color="#e25a8a"/><stop offset="1" stop-color="#7b5a4c"/></linearGradient></defs>
    <rect width="250" height="395" fill="url(#heroG)"/>
  </svg>
</header>

<section class="about-text">
  <h2 class="heading section-title">About<small>Quelborn Fitness</small></h2>
  <p class="para">Quelborn Fitness is the home of a former elite gymnast from Russia who now trains clients across Lodi. Every session blends strength, balance and joy, so you move better, feel lighter and reach any goal with a smile.</p>
  <a class="btn section-btn">Read More</a>
</section>
<svg class="photo" style="left:595px;top:655px" width="475" height="285" role="img" aria-label="Video of an outdoor group workout on grass">
  <defs><linearGradient id="vidG" x1="0" y1="0" x2="1" y2="1"><stop offset="0" stop-color="#8fa86a"/><stop offset="1" stop-color="#4d6a35"/></linearGradient></defs>
  <rect width="475" height="285" fill="url(#vidG)"/>
  <circle cx="237" cy="142" r="38" fill="#ffffff" opacity="0.85"/>
  <polygon points="225,122 225,162 257,142" fill="#333"/>
</svg>

<div class="group-band"></div>
<svg class="photo" style="left:0;top:1025px" width="600" height="465" role="img" aria-label="Group of smiling clients exercising together in a park">
  <defs><linearGradient id="grpG" x1="0" y1="0" x2="0" y2="1"><stop offset="0" stop-color="#6f8f4a"/><stop offset="0.6" stop-color="#a6b36c"/><stop offset="1" stop-color="#5c7a33"/></linearGradient></defs>
  <rect width="600" height="465" fill="url(#grpG)"/>
</svg>
<section class="group-text">
  <h2 class="heading section-title">Group<small>Classes/Boot Camps</small></h2>
  <p class="para">Outdoor boot camps and group classes built for every level. Small teams, friendly energy and fresh air make each workout fun, challenging and easy to stick with week after week.</p>
  <a class="btn section-btn">Read More</a>
</section>

<div class="personal-band"></div>
<section class="personal-text">
  <h2 class="heading section-title">Personal<small>Training</small></h2>
  <p class="para">One to one coaching shaped around your body, your goals and your schedule. From elite athletes to clients with disabilities, every plan is safe, personal and built to last.</p>
  <a class="btn section-btn">Read More</a>
</section>
<svg class="photo" style="left:600px;top:1475px" width="600" height="440" role="img" aria-label="Trainer in blue top doing an aerial stretch among trees">
  <defs><linearGradient id="perG" x1="0" y1="0" x2="1" y2="1"><stop offset="0" stop-color="#3f5a2a"/><stop offset="0.5" stop-color="#6e8c4c"/><stop offset="1" stop-color="#2f4a22"/></linearGradient></defs>
  <rect width="600" height="440" fill="url(#perG)"/>
</svg>

<svg class="photo" style="left:0;top:1920px" width="1200" height="415" role="img" aria-label="Trainer stretching outdoors on a lawn, darkened backdrop">
  <defs><linearGradient id="tesG" x1="0" y1="0" x2="1" y2="0"><stop offset="0" stop-color="#2e2f2a"/><stop offset="0.6" stop-color="#4a4a40"/><stop offset="1" stop-color="#6a7050"/></linearGradient></defs>
  <rect width="1200" height="415" fill="url(#tesG)"/>
</svg>
<section class="testimonial-text">
  <h2 class="heading section-title">Client<small>Testimonials</small></h2>
  <p class="para">“Training with her changed how I feel every single day. I am stronger, calmer and finally enjoy exercise. Each session is positive, focused and full of good humour.”</p>
  <div class="quote-name">— Renata Olsen</div>
  <div class="arrows">
    <span><svg width="8" height="10"><polyline points="6,1 2,5 6,9" fill="none" stroke="#fff" stroke-width="1.5"/></svg></span>
    <span><svg width="8" height="10"><polyline points="2,1 6,5 2,9" fill="none" stroke="#fff" stroke-width="1.5"/></svg></span>
  </div>
</section>

<section class="subscribe">
  <h2 class="heading">Subscribe Advise/Tips</h2>
  <div class="form">
    <div class="field">First Name</div>
    <div class="field">Last Name</div>
    <div class="field">Email Address</div>
    <div class="submit">SIGN UP</div>
  </div>
</section>

<footer>
  <nav class="footer-nav"><span>Home</span><span class="sep">|</span><span>Group Classes</span><span class="sep">|</span><span>Personal Training</span><span class="sep">|</span><span>About Irina</span><span class="sep">|</span><span>Contact</span><span class="sep">|</span><span>Blog</span></nav>
  <div class="social"><i></i><i></i><i></i></div>
  <div class="copyright">© 2024 Quelborn Fitness Lodi. All rights reserved.</div>
</footer>

</body>
</html>
```